A website for a Maltese Law Firm

Our law firm needs a website to further its business. The site should have a simple yet effective design. We would need the following sections: About us, Practice Areas, About Malta, Contact. These should be further split as follows:

About us: Our firm, Our values, What others say, Offices

Practice Areas: Crimimal, Citizenship & Residence, Sovereign Patron Pathway, Criminal Defence, Civil Litigation, Arbitration and ADR, Commercial and Corporate, Media Law.

About Malta: just one section.

Contact: Just one section

We would also need a news feed at the front of the site to include latest news regarding our cases.

At the bottom we need a section for our Terms and a Privacy Statement.

Our logo is being attached.

Target Market(s)

All clients looking for legal assistance in Malta

Industry/Entity Type

Legal

Coding

Coded - Design and coding required

Number of Pages Required

1 page

Requirements
Must have
• It must be simple yet striking.

```html
<!DOCTYPE html>
<html lang="en">
<head>
<meta charset="utf-8">
<title>Marlowe &amp; Strand Advocates</title>
<link href="https://fonts.googleapis.com/css2?family=Cinzel:wght@400;600&family=Lato:wght@400;700&family=Questrial&display=swap" rel="stylesheet">
<style>
:root{
  --ink:#1e1e1e;
  --muted:#9a9a9a;
  --soft-bg:#f1f1f1;
  --white:#ffffff;
  --nav:#2b2b2b;
  --nav-active:#cfcfcf;
  --footer:#2a2a2a;
  --footer-text:#b9b9b9;
  --bottom:#1b1b1b;
  --rule:#cfcfcf;
  --sky-top:#3f86d8;
  --sky-bottom:#bcdcf5;
}
*{box-sizing:border-box;margin:0;padding:0}
html,body{width:1200px;height:2535px;overflow:hidden;background:var(--white)}
body{position:relative;font-family:"Lato",sans-serif;color:var(--ink)}
.abs{position:absolute}

/* header */
.site-header{position:absolute;left:0;top:0;width:1200px;height:120px;background:var(--white);z-index:10}
.brand{left:101px;top:28px;font-family:"Cinzel",serif;font-weight:600;font-size:30px;letter-spacing:1px;color:var(--ink);line-height:1.2}
.brand-sub{display:block}
.header-contact{right:100px;top:26px;text-align:right;font-size:16px;line-height:30px;color:var(--ink)}
.header-contact svg{vertical-align:middle;margin-right:8px}
.main-nav{left:100px;top:101px;width:1002px;height:41px;background:var(--nav);display:flex;z-index:11}
.main-nav a{color:var(--white);text-decoration:none;font-size:16px;font-weight:700;text-transform:uppercase;display:flex;align-items:center;justify-content:center;border-right:1px solid #555;height:100%}
.main-nav a.active{background:var(--nav-active);color:var(--ink)}

/* hero */
.hero{left:0;top:120px;width:1200px;height:514px;background:linear-gradient(160deg,#dbe7f3 0%,#8fb0d2 45%,#3f6a98 100%);z-index:1}
.hero-arrow{top:218px}
.hero-caption{left:0;top:433px;width:1200px;height:81px;background:rgba(40,40,40,.72)}
.hero-caption p{position:absolute;left:101px;top:26px;font-family:"Cinzel",serif;font-weight:600;font-size:21px;color:var(--white);letter-spacing:.5px}
.btn-consult{position:absolute;left:853px;top:20px;width:247px;height:42px;background:var(--white);font-family:"Cinzel",serif;font-weight:600;font-size:15px;color:var(--ink);display:flex;align-items:center;justify-content:center}

/* section titles */
.section-title{width:1200px;left:0;text-align:center;font-family:"Cinzel",serif;font-size:27px;letter-spacing:1px;color:var(--ink)}
.section-title span{color:var(--muted)}
.title-rule{left:360px;width:478px;height:1px;background:var(--rule)}
.title-rule::after{content:"";position:absolute;left:203px;top:-2px;width:74px;height:4px;background:#444}

/* practice */
.practice{left:0;top:634px;width:1200px;height:366px;background:var(--soft-bg)}
.practice-item{top:170px;width:240px;text-align:center}
.practice-item svg{display:block;margin:0 auto 16px}
.practice-item h3{font-family:"Cinzel",serif;font-weight:600;font-size:23px;line-height:29px;color:var(--ink)}
.circle-arrow{width:34px;height:34px}

/* welcome */
.welcome{left:0;top:1000px;width:1200px;height:441px;background:var(--white);overflow:hidden}
.sky{left:0;top:0;width:1200px;height:441px}
.welcome h2{position:absolute;left:101px;top:48px;font-family:"Cinzel",serif;font-size:27px;color:var(--ink);font-weight:600}
.welcome h2 span{color:var(--muted);font-weight:400}
.welcome-rule{left:101px;top:100px;width:183px;height:2px;background:#444}
.welcome-lead{left:101px;top:116px;width:495px;font-size:17.5px;line-height:26px;font-family:"Questrial",sans-serif}
.checks{left:101px;top:210px;width:460px;list-style:none;font-family:"Questrial",sans-serif;font-size:14.5px;line-height:21px}
.checks li{position:relative;padding-left:36px;margin-bottom:10px}
.checks svg{position:absolute;left:0;top:0}
.btn-more{left:101px;top:357px;width:109px;height:34px;background:#555;color:var(--white);font-size:13px;font-weight:700;display:flex;align-items:center}
.btn-more span{padding-left:7px;flex:1}
.btn-more i{width:30px;height:34px;background:#1a1a1a;display:flex;align-items:center;justify-content:center}
.video{left:622px;top:102px;width:480px;height:294px;background:#111}
.video-frame{left:0;top:0;width:480px;height:268px;background:linear-gradient(135deg,#e6e3df 0%,#8a5a3c 55%,#3a2418 100%)}
.video-bar{left:0;top:268px;width:480px;height:26px;background:#1c1c1c}

/* testimonials */
.testimonials{left:0;top:1441px;width:1200px;height:379px;background:var(--soft-bg)}
.avatar{width:94px;height:94px;border-radius:50%;border:4px solid #444;background:linear-gradient(180deg,#c9c2ba,#7d8fa6)}
.avatar-tail{width:0;height:0;border-left:9px solid transparent;border-right:9px solid transparent;border-top:12px solid #444}
.client-name{font-size:13px;font-weight:700}
.quote{width:318px;font-family:"Questrial",sans-serif;font-size:12.5px;line-height:22px;color:#333}
.quote b{font-family:"Cinzel",serif;color:#ccc;font-size:26px;line-height:0;vertical-align:-6px}
.divider-v{left:611px;top:155px;width:1px;height:150px;background:#d5d5d5}

/* cases */
.cases{left:0;top:1820px;width:1200px;height:287px;background:var(--white)}
.case{top:167px;width:475px;display:flex}
.date{width:46px;flex:none;margin-right:14px;text-align:center}
.date .day{background:#111;color:var(--white);font-size:20px;font-weight:700;height:34px;line-height:34px}
.date .mon{background:#666;color:var(--white);font-size:10px;font-weight:700;height:20px;line-height:20px}
.case h4{font-size:14.5px;font-weight:700;margin-bottom:6px}
.case p{font-family:"Questrial",sans-serif;font-size:15px;line-height:24px;color:#555}
.case-divider{left:599px;top:165px;width:1px;height:72px;background:#ddd}

/* footer */
.site-footer{left:0;top:2107px;width:1200px;height:281px;background:var(--footer);color:var(--footer-text)}
.foot-title{font-family:"Cinzel",serif;font-size:16px;color:#e6e6e6;letter-spacing:.5px}
.foot-rule{height:1px;background:#444}
.quick-links{list-style:none;font-size:12.5px;line-height:28.5px}
.quick-links li::before{content:"› ";color:#777}
.contact-list{font-size:12.5px;line-height:20px}
.contact-list .row{display:flex;align-items:center;gap:10px;margin-top:20px}
.field{left:519px;width:270px;background:var(--white);font-size:11px;font-style:italic;color:#555;padding:7px 10px}
.btn-submit{left:519px;top:212px;width:125px;height:33px;background:#5a5a5a;color:var(--white);font-weight:700;font-size:16px;display:flex;align-items:center;justify-content:center}
.foot-sep{left:820px;top:40px;width:1px;height:200px;background:#444}
.foot-brand{left:858px;top:82px;width:234px;text-align:center;font-family:"Cinzel",serif;font-size:20px;color:#e6e6e6;line-height:1.15}
.follow{left:858px;top:155px;width:234px;text-align:center;font-family:"Cinzel",serif;font-size:15px;color:#e6e6e6}
.socials{left:912px;top:184px;display:flex;gap:8px}
.socials i{width:22px;height:22px;display:block}

.disclaimer{left:0;top:2388px;width:1200px;height:112px;background:#eeeeee;padding:20px 130px 0;text-align:center;font-size:12.5px;line-height:22px;color:#333}
.copyright{left:0;top:2500px;width:1200px;height:35px;background:var(--bottom);color:#ccc;font-size:12px;text-align:center;line-height:35px}
</style>
</head>
<body>

<header class="site-header">
  <div class="abs brand">Marlowe &amp; Strand<span class="brand-sub" style="font-size:13px;letter-spacing:6px;padding-left:92px">Advocates</span></div>
  <div class="abs header-contact">
    <div><svg width="16" height="16" viewBox="0 0 24 24"><path fill="#1e1e1e" d="M6.6 10.8a15 15 0 0 0 6.6 6.6l2.2-2.2c.3-.3.7-.4 1-.2 1.1.4 2.3.6 3.6.6.6 0 1 .4 1 1V20c0 .6-.4 1-1 1C10.6 21 3 13.4 3 4c0-.6.4-1 1-1h3.5c.6 0 1 .4 1 1 0 1.3.2 2.5.6 3.6.1.3 0 .7-.2 1z"/></svg>123-456-7890</div>
    <div><svg width="20" height="14" viewBox="0 0 20 14"><rect width="20" height="14" fill="#1e1e1e"/><path d="M1 1l9 7 9-7" stroke="#fff" stroke-width="1.5" fill="none"/></svg>info@marlowestrand.com</div>
  </div>
  <nav class="abs main-nav">
    <a class="active" style="width:86px">Home</a>
    <a style="width:142px">About Malta</a>
    <a style="width:175px">Practice Areas</a>
    <a style="width:117px">Our Firm</a>
    <a style="width:138px">Our Values</a>
    <a style="width:192px">What Others Say</a>
    <a style="width:152px;border-right:0">Contact Us</a>
  </nav>
</header>

<section class="abs hero" role="img" aria-label="Business people shaking hands in a bright office, blurred behind a desk with papers">
  <svg class="abs hero-arrow" style="left:44px" width="22" height="40" viewBox="0 0 22 40"><path d="M18 4L4 20l14 16" stroke="#fff" stroke-width="3" fill="none"/></svg>
  <svg class="abs hero-arrow" style="left:1134px" width="22" height="40" viewBox="0 0 22 40"><path d="M4 4l14 16L4 36" stroke="#fff" stroke-width="3" fill="none"/></svg>
  <div class="abs hero-caption">
    <p>Realize Your Constitutional Right For Qualified Legal Help</p>
    <div class="btn-consult">Get A Free Consultation</div>
  </div>
</section>

<section class="abs practice">
  <h2 class="abs section-title" style="top:30px">Our <span>Practice Areas</span></h2>
  <div class="abs title-rule" style="top:104px"></div>
  <svg class="abs circle-arrow" style="left:47px;top:217px" viewBox="0 0 34 34"><circle cx="17" cy="17" r="15" fill="none" stroke="#c4c4c4" stroke-width="2"/><path d="M20 10l-7 7 7 7" stroke="#c4c4c4" stroke-width="3" fill="none"/></svg>
  <svg class="abs circle-arrow" style="left:1117px;top:217px" viewBox="0 0 34 34"><circle cx="17" cy="17" r="15" fill="none" stroke="#444" stroke-width="2"/><path d="M14 10l7 7-7 7" stroke="#444" stroke-width="3" fill="none"/></svg>

  <div class="abs practice-item" style="left:105px;top:170px">
    <svg width="70" height="80" viewBox="0 0 70 80"><rect x="22" y="2" width="42" height="60" rx="4" fill="#1e1e1e"/><rect x="6" y="14" width="44" height="62" rx="4" fill="#1e1e1e" stroke="#f1f1f1" stroke-width="3"/><circle cx="28" cy="42" r="12" fill="none" stroke="#f1f1f1" stroke-width="2.5"/><path d="M16 42h24M28 30v24" stroke="#f1f1f1" stroke-width="2"/></svg>
    <h3>Citizenship &amp;<br>Residence</h3>
  </div>
  <div class="abs practice-item" style="left:346px;top:170px">
    <svg width="80" height="80" viewBox="0 0 80 80"><rect x="24" y="10" width="24" height="14" rx="2" transform="rotate(35 36 17)" fill="#1e1e1e"/><path d="M34 28L14 56" stroke="#1e1e1e" stroke-width="6"/><rect x="10" y="62" width="50" height="8" fill="#1e1e1e"/></svg>
    <h3>Civil<br>Litigation</h3>
  </div>
  <div class="abs practice-item" style="left:596px;top:170px">
    <svg width="80" height="80" viewBox="0 0 80 80"><rect x="28" y="10" width="24" height="12" rx="3" fill="none" stroke="#1e1e1e" stroke-width="5"/><rect x="8" y="20" width="64" height="50" rx="7" fill="#1e1e1e"/><circle cx="40" cy="45" r="14" fill="#fff"/><path d="M40 37v16M32 45h16" stroke="#1e1e1e" stroke-width="5"/></svg>
    <h3>Health<br>Care Law</h3>
  </div>
  <div class="abs practice-item" style="left:843px;top:170px">
    <svg width="80" height="80" viewBox="0 0 80 80"><rect x="32" y="22" width="16" height="56" rx="6" fill="#1e1e1e"/><circle cx="40" cy="16" r="14" fill="#1e1e1e"/><circle cx="40" cy="16" r="6" fill="#f1f1f1"/></svg>
    <h3>Media<br>Law</h3>
  </div>
</section>

<section class="abs welcome">
  <svg class="abs sky" viewBox="0 0 1200 441" role="img" aria-label="Bright blue sky with sun and clouds">
    <defs><linearGradient id="skyGrad" x1="0" y1="0" x2="0" y2="1"><stop offset="0" stop-color="#3f86d8"/><stop offset="1" stop-color="#bcdcf5"/></linearGradient></defs>
    <polygon points="811,0 1200,0 1200,441 693,441" fill="url(#skyGrad)"/>
  </svg>
  <h2>Welcome To <span>Marlowe &amp; Strand Advocates</span></h2>
  <div class="abs welcome-rule"></div>
  <p class="abs welcome-lead">Lorem ipsumn sit amet co adipisclitsedudml eiusmo dtepor incidiunt ut la dolore ma aliquanmi kni enim nim veni exercitation ullamco ips sdlitnol ameti co adipiscig</p>
  <ul class="abs checks">
    <li><svg width="24" height="24" viewBox="0 0 24 24"><circle cx="11" cy="13" r="9" fill="none" stroke="#333" stroke-width="1.6"/><path d="M6 12l5 5 10-13" stroke="#333" stroke-width="2" fill="none"/></svg>Lorem ipsumn sit amet co adipisclitsedudml eiusmo dtepor incidiunt ut la dolore ma aliquanmi kni enim nim veni</li>
    <li><svg width="24" height="24" viewBox="0 0 24 24"><circle cx="11" cy="13" r="9" fill="none" stroke="#333" stroke-width="1.6"/><path d="M6 12l5 5 10-13" stroke="#333" stroke-width="2" fill="none"/></svg>Lorem ipsumn sit amet co adipisclitsedudml eiusmo</li>
    <li><svg width="24" height="24" viewBox="0 0 24 24"><circle cx="11" cy="13" r="9" fill="none" stroke="#333" stroke-width="1.6"/><path d="M6 12l5 5 10-13" stroke="#333" stroke-width="2" fill="none"/></svg>Lorem ipsumn sit amet co adipisclitsedudml eiusmo dtepor incidiunt ut la dolore ma aliquanmi kni enim nim venim.</li>
  </ul>
  <div class="abs btn-more"><span>Read More</span><i><svg width="12" height="12" viewBox="0 0 12 12"><path d="M1 1l5 5-5 5M6 1l5 5-5 5" stroke="#fff" stroke-width="1.6" fill="none"/></svg></i></div>
  <div class="abs video">
    <div class="abs video-frame" role="img" aria-label="Video still of a judge's gavel beside a hand signing a document"></div>
    <svg class="abs" style="left:208px;top:112px" width="64" height="44" viewBox="0 0 64 44"><rect width="64" height="44" rx="10" fill="#333" fill-opacity=".85"/><path d="M26 13l14 9-14 9z" fill="#fff"/></svg>
    <div class="abs video-bar">
      <svg class="abs" style="left:10px;top:8px" width="10" height="10" viewBox="0 0 10 10"><path d="M1 0l8 5-8 5z" fill="#aaa"/></svg>
      <div class="abs" style="left:30px;top:12px;width:420px;height:2px;background:#555"></div>
    </div>
  </div>
</section>

<section class="abs testimonials">
  <h2 class="abs section-title" style="top:62px">Client <span>Testimonials</span></h2>
  <div class="abs title-rule" style="top:102px"></div>
  <svg class="abs circle-arrow" style="left:47px;top:200px" viewBox="0 0 34 34"><circle cx="17" cy="17" r="15" fill="none" stroke="#c4c4c4" stroke-width="2"/><path d="M20 10l-7 7 7 7" stroke="#c4c4c4" stroke-width="3" fill="none"/></svg>
  <svg class="abs circle-arrow" style="left:1117px;top:200px" viewBox="0 0 34 34"><circle cx="17" cy="17" r="15" fill="none" stroke="#444" stroke-width="2"/><path d="M14 10l7 7-7 7" stroke="#444" stroke-width="3" fill="none"/></svg>

  <div class="abs avatar" style="left:113px;top:160px" role="img" aria-label="Portrait photo of client John Doe"></div>
  <div class="abs avatar-tail" style="left:151px;top:254px"></div>
  <div class="abs client-name" style="left:124px;top:286px">- John Doe</div>
  <p class="abs quote" style="left:232px;top:165px"><b>“</b> Lorem ipsumn sit amet co adipisclitsedudml eiusmo dtepor incidiunt ut la dolore ma aliquanmi kni enim nim veni exercitation ullamco ips sdlitnol ameti co adipiscig elitsed do eiusmod te epo uom Accusant dol oremque laudantium. <b>”</b></p>

  <div class="abs divider-v"></div>

  <div class="abs avatar" style="left:671px;top:160px" role="img" aria-label="Portrait photo of client Nora Vell"></div>
  <div class="abs avatar-tail" style="left:709px;top:254px"></div>
  <div class="abs client-name" style="left:676px;top:286px">- Nora Vell</div>
  <p class="abs quote" style="left:786px;top:165px"><b>“</b> Lorem ipsumn sit amet co adipisclitsedudml eiusmo dtepor incidiunt ut la dolore ma aliquanmi kni enim nim veni exercitation ullamco ips sdlitnol ameti co adipiscig elitsed do eiusmod te epo uom Accusant dol oremque laudantium. <b>”</b></p>
</section>

<section class="abs cases">
  <h2 class="abs section-title" style="top:60px">Recent Case <span>Studies</span></h2>
  <div class="abs title-rule" style="top:103px"></div>
  <svg class="abs" style="left:64px;top:187px" width="18" height="30" viewBox="0 0 18 30"><path d="M15 2L3 15l12 13" stroke="#333" stroke-width="2" fill="none"/></svg>
  <svg class="abs" style="left:1118px;top:187px" width="18" height="30" viewBox="0 0 18 30"><path d="M3 2l12 13L3 28" stroke="#333" stroke-width="2" fill="none"/></svg>
  <article class="abs case" style="left:108px">
    <div class="date"><div class="day">08</div><div class="mon">JUNE</div></div>
    <div><h4>Sed ut perspiciatis unde omnis iste natus error sit</h4><p>Accusant &nbsp;doloremque laudantium, totamrem aperiam, moregi eaquemn ipsa quae ab illoi facilies.</p></div>
  </article>
  <div class="abs case-divider"></div>
  <article class="abs case" style="left:634px">
    <div class="date"><div class="day">08</div><div class="mon">JUNE</div></div>
    <div><h4>Sed ut perspiciatis unde omnis iste natus error sit</h4><p>Accusant &nbsp;doloremque laudantium, totamrem aperiam, moregi eaquemn ipsa quae ab illoi facilies.</p></div>
  </article>
</section>

<footer class="abs site-footer">
  <div class="abs foot-title" style="left:101px;top:32px">Quick Links</div>
  <div class="abs foot-rule" style="left:101px;top:58px;width:148px"></div>
  <ul class="abs quick-links" style="left:101px;top:64px">
    <li>Home</li><li>About Malta</li><li>Practice Areas</li><li>Our Firm</li><li>Our Values</li><li>What Others Say</li><li>Contact Us</li>
  </ul>

  <div class="abs foot-title" style="left:275px;top:32px">Contact Details</div>
  <div class="abs foot-rule" style="left:275px;top:58px;width:200px"></div>
  <div class="abs contact-list" style="left:275px;top:66px;width:210px">
    <div>Marlowe &amp; Strand Advocates<br>123, Dollar Smt Amey, Noumy,<br>Goham, Domalkg - 123 456</div>
    <div class="row"><svg width="12" height="12" viewBox="0 0 24 24"><path fill="#ddd" d="M6.6 10.8a15 15 0 0 0 6.6 6.6l2.2-2.2c.3-.3.7-.4 1-.2 1.1.4 2.3.6 3.6.6.6 0 1 .4 1 1V20c0 .6-.4 1-1 1C10.6 21 3 13.4 3 4c0-.6.4-1 1-1h3.5c.6 0 1 .4 1 1 0 1.3.2 2.5.6 3.6.1.3 0 .7-.2 1z"/></svg>123-456-7890</div>
    <div class="row"><svg width="13" height="12" viewBox="0 0 13 12"><rect x="3" y="0" width="7" height="4" fill="#ddd"/><rect x="0" y="4" width="13" height="5" fill="#ddd"/><rect x="3" y="8" width="7" height="4" fill="#ddd"/></svg>123-456-7890</div>
    <div class="row"><svg width="13" height="9" viewBox="0 0 20 14"><rect width="20" height="14" fill="#ddd"/><path d="M1 1l9 7 9-7" stroke="#2a2a2a" stroke-width="2" fill="none"/></svg>info@marlowestrand.com</div>
  </div>

  <div class="abs foot-title" style="left:520px;top:32px">Quick Inquiry</div>
  <div class="abs foot-rule" style="left:520px;top:58px;width:270px"></div>
  <div class="abs field" style="top:73px;height:34px">Name</div>
  <div class="abs field" style="top:112px;height:34px">Phone</div>
  <div class="abs field" style="top:151px;height:49px">Message</div>
  <div class="abs btn-submit">Submit</div>

  <div class="abs foot-sep"></div>
  <div class="abs foot-brand">Marlowe &amp; Strand<br><span style="font-size:11px;letter-spacing:5px">Advocates</span></div>
  <div class="abs follow">Follow Us On</div>
  <div class="abs socials" aria-label="Social profiles">
    <i style="background:#3b5a98"></i><i style="background:#0a77b5"></i><i style="background:#2ba3e0"></i><i style="background:#d34836"></i>
  </div>
</footer>

<div class="abs disclaimer"><b>Disclaimer</b> : Lorem ipsum dolor sit amet, consectetur adipiscing elit. Mauris ut mattis elit, fringilla interdum urna. Integer venenatis sollicitudin tortor, sit amet volutpat turpis lobortis ut. Etiam euismod diam sagittis feugiat egestas. Aenean urna ipsum, viverra sed commodo sit amet, cursus et tellus. Curabitur vulputate risus at enim egestas, eget porta justo porta. Vestibulum et quam sed neque faucibus faucibus &nbsp;pellentesque gravida pellentesque non</div>
<div class="abs copyright">Copyright © 2016 Marlowe &amp; Strand Advocates. All Rights Reserved.</div>

</body>
</html>
```